Geschäftspapiere für junges Unternehmen aus dem Garten- und Landschaftsbau
Zielgruppe
Wir sind ein junges Unternehmen im Bereich Garten und Landschaftsbau, wir beschäftigen uns mit pflege von Gärten sowie die Neu und Umgestaltung von Gärten. Unsere Zielguppe ist der Privatgarten und zum kleinen Teil auch Gewerbekunden.
Aufgabenstellung
Es sollen die Elemente der Bilder beinhalten, der Nachname und die Branchenbezeichnung enthalten sein. Die Fußzeile des Geschäftpapiers sind vorgesehen und die Daten werden erst angegeben wenn der bestimmte Entwurf mir zusagt.

```html
<!DOCTYPE html>
<html lang="de">
<head>
<meta charset="utf-8">
<title>Briefbogen – Torem Vasch Garten und Landschaftsbau</title>
<link href="https://fonts.googleapis.com/css2?family=Carlito:ital,wght@0,400;0,700;1,700&display=swap" rel="stylesheet">
<style>
  :root {
    --backdrop: #e9e9e7;
    --paper: #ffffff;
    --forest-dark: #18241f;
    --forest-mid: #31493f;
    --forest-mist: #4d6f66;
    --green-deep: #1a5e2c;
    --green-bright: #4caf3f;
    --ring-muted: #6b8a66;
    --ink: #1e1e1e;
    --ink-light: #f2f2f2;
  }
  * { margin: 0; padding: 0; box-sizing: border-box; }
  html, body {
    width: 966px; height: 1200px; overflow: hidden;
    background: var(--backdrop);
    font-family: "Carlito", "Calibri", sans-serif;
    color: var(--ink);
  }
  .letterhead {
    position: absolute; left: 73px; top: 21px;
    width: 820px; height: 1158px;
    background: var(--paper);
    box-shadow: 0 2px 10px rgba(0,0,0,.12);
    overflow: hidden;
  }
  .header-band {
    position: absolute; left: 0; top: 0; width: 100%; height: 184px;
    background:
      linear-gradient(90deg, rgba(24,36,31,.55) 0%, rgba(24,36,31,0) 30%, rgba(24,36,31,0) 70%, rgba(24,36,31,.6) 100%),
      linear-gradient(180deg, var(--forest-dark) 0%, var(--forest-mid) 55%, var(--forest-mist) 100%);
  }
  .brand-mark {
    position: absolute; left: 89px; top: 25px;
    width: 128px; height: 128px;
    border-radius: 50%;
    border: 9px solid var(--ring-muted);
    display: flex; align-items: center; justify-content: center;
  }
  .brand-name {
    font-weight: 700; font-size: 22px; color: var(--green-bright);
  }
  .tagline {
    position: absolute; left: 291px; top: 36px;
    font-style: italic; font-weight: 700; font-size: 28px; line-height: 36px;
    color: var(--ink-light);
  }
  .contact {
    position: absolute; top: 134px;
    font-weight: 700; font-size: 12px; line-height: 15px; color: var(--ink-light);
    display: flex; gap: 8px;
  }
  .contact svg { flex: none; margin-top: 1px; }
  .contact--address { left: 299px; }
  .contact--reach { left: 461px; }
  .icon-stack { display: flex; flex-direction: column; gap: 4px; }
  .sender-line {
    position: absolute; left: 108px; top: 206px;
    font-size: 10.5px;
  }
  .sender-line .sender-name { color: var(--green-bright); font-weight: 700; }
  .footer-rule {
    position: absolute; left: 66px; top: 1058px; width: 581px; height: 2.5px;
    background: var(--green-deep);
  }
  .footer-col {
    position: absolute; top: 1090px;
    font-size: 12.5px; line-height: 17px;
  }
  .footer-col--owner { left: 66px; }
  .footer-col--bank { left: 268px; }
  .footer-col--account { left: 434px; }
  .footer-divider {
    position: absolute; top: 1088px; width: 1.5px; height: 36px;
    background: var(--green-bright);
  }
  .footer-divider--one { left: 250px; }
  .footer-divider--two { left: 415px; }
  .tree-decoration {
    position: absolute; left: 681px; top: 1029px; width: 125px; height: 123px;
    background: linear-gradient(90deg, var(--green-deep) 0%, var(--green-deep) 45%, var(--green-bright) 60%, var(--green-bright) 100%);
    opacity: .9;
  }
  .bottom-band {
    position: absolute; left: 0; top: 1152px; width: 100%; height: 6px;
    background: var(--green-deep);
  }
</style>
</head>
<body>
<main class="letterhead">
  <header class="header-band" role="img" aria-label="Foto eines nebligen Nadelwalds">
  </header>

  <div class="brand-mark">
    <span class="brand-name">Vasch</span>
  </div>

  <h1 class="tagline">Garten und Landschaftsbau<br>Weihnachtsbäume Baumfällung</h1>

  <div class="contact contact--address">
    <svg width="9" height="11" viewBox="0 0 10 13" aria-hidden="true">
      <path d="M5 0C2.2 0 0 2.2 0 5c0 3.5 5 8 5 8s5-4.5 5-8c0-2.8-2.2-5-5-5zm0 7a2 2 0 1 1 0-4 2 2 0 0 1 0 4z" fill="var(--ink-light)"/>
    </svg>
    <address style="font-style:normal">Lindenhangstrasse 12<br>55599 Waldhofen</address>
  </div>

  <div class="contact contact--reach">
    <div class="icon-stack">
      <svg width="11" height="11" viewBox="0 0 12 12" aria-hidden="true">
        <path d="M2.5 0.5l2 2.3-1.1 1.4c.7 1.6 2 2.9 3.6 3.6l1.4-1.1 2.3 2-1 2c-5 .2-9.3-4.1-9.2-9.2z" fill="var(--ink-light)"/>
      </svg>
      <svg width="12" height="9" viewBox="0 0 12 9" aria-hidden="true">
        <rect x="0" y="0" width="12" height="9" fill="var(--ink-light)"/>
        <path d="M0 0l6 5 6-5M0 9l4.5-4.5M12 9L7.5 4.5" stroke="var(--forest-mid)" stroke-width="1.2" fill="none"/>
      </svg>
    </div>
    <div>torem.vasch@postwelle.de<br>M 017 00 12 34 56</div>
  </div>

  <p class="sender-line"><span class="sender-name">Torem Vasch I</span> Lindenhangstrasse 12, 55599 Waldhofen</p>

  <div class="footer-rule"></div>

  <div class="footer-col footer-col--owner">Torem Vasch<br>Steurliche ID: DE 000123456</div>
  <div class="footer-divider footer-divider--one"></div>
  <div class="footer-col footer-col--bank">Bankwerbindung:<br>Auenbank Berlin</div>
  <div class="footer-divider footer-divider--two"></div>
  <div class="footer-col footer-col--account">BIC: AUENDEXX000<br>IBAN: DE00 1234 5678 0000 0000 00</div>

  <div class="tree-decoration" role="img" aria-label="Illustration einer Tanne und eines Laubbaums"></div>

  <div class="bottom-band"></div>
</main>
</body>
</html>
```